Stylish new business card needed!

Hello everyone! I am in need of a new business card design for an alarm company here in Hurricane WV. I have all fonts, color codes and logos provided for you use! We are a young company and like the style of a clean sleek looking business card. Would like it double sided, one side holding the logo and the other with your design!
Target Market(s)
The people that are looking for the newest tech for home automation and security
Industry/Entity Type
Alarm services; Home automation
Contact Information for Business Card
Name of person; position (Sales; Installer); Phone Number (555.418.7260); Employee cell Number; Website (www.GuardedByVelk.example); Employee Email; Double sided
Look and feel
Each slider illustrates characteristics of the customer's brand and the style your logo design should communicate.

```html
<!DOCTYPE html>
<html lang="en">
<head>
<meta charset="utf-8">
<title>Guarded By Velk – Business Card</title>
<link href="https://fonts.googleapis.com/css2?family=Arimo:wght@400;700&display=swap" rel="stylesheet">
<style>
  :root {
    --stage: #2b2b2f;
    --card: #1f1f23;
    --orange: #f08c4a;
    --grey: #9a9a9a;
    --white: #ffffff;
  }
  * { box-sizing: border-box; margin: 0; padding: 0; }
  html, body { width: 1200px; height: 780px; overflow: hidden; }
  body {
    background: var(--stage);
    font-family: "Arimo", Arial, sans-serif;
    display: flex;
    align-items: center;
    justify-content: center;
    gap: 40px;
  }
  .card {
    position: relative;
    width: 550px;
    height: 330px;
    background: var(--card);
    border-radius: 22px;
    border-bottom: 4px solid var(--orange);
    border-left: 2px solid var(--orange);
    box-shadow: 0 14px 30px rgba(0,0,0,.45);
    overflow: hidden;
  }

  /* brand lockup */
  .brand { text-align: center; }
  .brand-name {
    color: var(--orange);
    font-weight: 700;
    letter-spacing: 3px;
    text-transform: uppercase;
    line-height: 1.05;
  }
  .brand-tagline {
    color: var(--orange);
    font-weight: 700;
    text-transform: uppercase;
    letter-spacing: 1px;
    margin-top: 12px;
  }

  /* front */
  .card-front { display: flex; align-items: center; justify-content: center; }
  .card-front .brand-name { font-size: 52px; }
  .card-front .brand-tagline { font-size: 13px; }

  /* back */
  .card-back .brand {
    position: absolute; left: 28px; top: 80px; width: 200px;
  }
  .card-back .brand-name { font-size: 34px; }
  .card-back .brand-tagline { font-size: 8px; letter-spacing: .5px; }
  .divider {
    position: absolute; left: 250px; top: 40px;
    width: 2px; height: 200px; background: var(--white);
  }
  .contact { position: absolute; left: 276px; top: 50px; }
  .person-name { font-size: 30px; font-weight: 700; color: var(--orange); }
  .person-name .surname { color: var(--grey); }
  .person-role { font-size: 15px; font-weight: 700; color: var(--white); margin-top: 4px; }
  .contact-list { list-style: none; margin-top: 24px; }
  .contact-list li {
    display: flex; align-items: center; gap: 10px;
    color: var(--white); font-size: 14px; line-height: 24px;
  }
  .contact-list svg { width: 14px; height: 14px; flex: none; }

  .footer-band {
    position: absolute; left: 0; right: 0; bottom: 18px;
    display: flex; align-items: center; height: 24px;
  }
  .band-orange { flex: 0 0 300px; height: 16px; background: var(--orange); }
  .band-mark {
    color: var(--grey); font-weight: 700; font-size: 24px;
    letter-spacing: 2px; padding: 0 10px; text-transform: uppercase;
  }
  .band-grey { flex: 1; height: 16px; background: var(--grey); }
</style>
</head>
<body>

  <section class="card card-front">
    <div class="brand">
      <div class="brand-name">Guarded By<br>Velk</div>
      <div class="brand-tagline">Automation and Security Services</div>
    </div>
  </section>

  <section class="card card-back">
    <div class="brand">
      <div class="brand-name">Guarded By<br>Velk</div>
      <div class="brand-tagline">Automation and Security Services</div>
    </div>

    <div class="divider"></div>

    <div class="contact">
      <div class="person-name">Lena <span class="surname">Marek</span></div>
      <div class="person-role">Sales; Installer</div>
      <ul class="contact-list">
        <li>
          <svg viewBox="0 0 16 16" aria-hidden="true"><path fill="var(--orange)" d="M3 1l3 3-2 2c1 2 3 4 5 5l2-2 3 3-2 3C7 15 1 9 0 4z"/></svg>
          555.418.7260
        </li>
        <li>
          <svg viewBox="0 0 16 16" aria-hidden="true"><rect x="4" y="1" width="8" height="14" rx="1.5" fill="none" stroke="var(--white)" stroke-width="1.5"/></svg>
          555.302.9184
        </li>
        <li>
          <svg viewBox="0 0 16 16" aria-hidden="true"><circle cx="8" cy="8" r="6.5" fill="none" stroke="var(--orange)" stroke-width="1.5"/><path d="M1.5 8h13M8 1.5c-3 3-3 10 0 13M8 1.5c3 3 3 10 0 13" fill="none" stroke="var(--orange)" stroke-width="1.2"/></svg>
          www.GuardedByVelk.example
        </li>
        <li>
          <svg viewBox="0 0 16 16" aria-hidden="true"><rect x="1" y="3" width="14" height="10" rx="1" fill="none" stroke="var(--orange)" stroke-width="1.5"/><path d="M1 4l7 5 7-5" fill="none" stroke="var(--orange)" stroke-width="1.5"/></svg>
          info@GuardedByVelk.example
        </li>
      </ul>
    </div>

    <div class="footer-band">
      <div class="band-orange"></div>
      <div class="band-mark">Velk</div>
      <div class="band-grey"></div>
    </div>
  </section>

</body>
</html>
```